Launch Website

A very simple, but attractive website (template preferred) is required in a common format - HTML5 or Wordpress etc.
It should be easily user updateable for updates.
Pages it needs:
-Home Page with menu bar, company logo and 1 large graphic/picture and two smaller graphics/logos.
- What we do
- How we do it
- About Us
- Guarantees
- Results
- Contact Page with Enquiry Form
- Provision for a blog to be added later

Most pages will be approx 150 words text with some small/medium images.
We have our own domain & hosting.

A "less is more" design approach would be encouraged.

Target Market(s)

Vehicle Fleet Managers

Industry/Entity Type

It Company

Font styles to use
Sans Serif

Colors
9bcb3c

Requirements
Must have
• Corporate Style. No Fluff.
Nice to have
• Images of LIght Commerical vehicles and trucks

Am ok with white background throughout site.
Colours should match/complement company logo.
Should not have
• Should not be too "busy"

```html
<!DOCTYPE html>
<html lang="en">
<head>
<meta charset="utf-8">
<title>ClearTune – Fleet Engine Optimisation</title>
<link rel="stylesheet" href="https://fonts.googleapis.com/css2?family=Roboto+Condensed:wght@400;500;700&family=Signika:wght@300;400&display=swap">
<style>
  :root {
    --brand-blue: #1a9bd7;
    --navy: #164b80;
    --navy-deep: #0f3c6b;
    --accent-red: #d62027;
    --text-grey: #9a9a9a;
    --text-dark: #555;
    --rule: #d9d9d9;
    --button: #cfcfcf;
    --footer: #efefef;
    --black: #050505;
  }
  * { box-sizing: border-box; margin: 0; padding: 0; }
  html, body { width: 1200px; height: 1003px; overflow: hidden; }
  body { position: relative; background: #fff; font-family: "Signika", sans-serif; color: var(--text-dark); }

  .site-header { position: absolute; left: 0; top: 0; width: 1200px; height: 103px;
    background: linear-gradient(#ffffff, #f1f1f1); }
  .brand { position: absolute; left: 131px; top: 30px; display: flex; align-items: center; gap: 10px;
    font-family: "Signika", sans-serif; font-size: 34px; font-weight: 400; color: var(--brand-blue); }
  .brand-dot { width: 22px; height: 22px; border-radius: 50%; background: var(--brand-blue); }
  .contact-strip { position: absolute; right: 132px; top: 26px; display: flex; align-items: center; gap: 4px; }
  .contact-strip svg { margin-top: 2px; }
  .contact-lines { font-size: 15px; color: #888; line-height: 19px; }
  .contact-lines .phone { color: var(--accent-red); font-size: 21px; }
  .contact-lines .email { color: #444; }

  .hero-band { position: absolute; left: 0; top: 103px; width: 1200px; height: 441px;
    background: linear-gradient(var(--navy-deep), var(--navy) 30%, #1c5a94); }
  .main-nav { position: absolute; left: 157px; top: 114px; width: 888px; display: flex; justify-content: space-between;
    font-family: "Roboto Condensed", sans-serif; font-weight: 500; font-size: 15px; color: #fff; letter-spacing: 0.2px; }

  .slider-frame { position: absolute; left: 131px; top: 155px; width: 937px; height: 468px; background: #fff;
    box-shadow: 0 18px 16px -14px rgba(0,0,0,0.45); }
  .slide-photo { position: absolute; left: 9px; top: 9px; width: 920px; height: 449px;
    background: linear-gradient(#8fb0d2 0%, #c5d6e6 45%, #a9a9aa 62%, #6f6c69 100%); }
  .slide-callout { position: absolute; left: 536px; top: 54px; width: 370px; height: 176px; }
  .callout-text { position: absolute; left: 612px; top: 84px; width: 290px; text-align: center;
    font-family: "Roboto Condensed", sans-serif; color: #fff; }
  .callout-text .lead { font-size: 24px; line-height: 28px; }
  .callout-text .save { color: var(--brand-blue); font-size: 19px; text-align: left; padding-left: 12px; line-height: 22px; }
  .callout-text .figure { color: var(--brand-blue); font-weight: 700; font-size: 28px; line-height: 48px; text-align: left; padding-left: 10px; }
  .callout-text .figure b { font-size: 50px; }
  .partner-badge { position: absolute; top: 363px; width: 128px; height: 77px; background: #fff; }
  .partner-badge span { position: absolute; left: 18px; top: 24px; width: 92px; height: 30px; border-radius: 3px; }
  .badge-one { left: 643px; } .badge-one span { background: #1f3f7a; }
  .badge-two { left: 781px; } .badge-two span { background: #7ec241; }
  .slider-dots { position: absolute; left: 29px; top: 431px; display: flex; gap: 4px; }
  .slider-dots i { width: 9px; height: 9px; background: #fff; }
  .slider-dots i.active { background: var(--brand-blue); }

  .teasers { position: absolute; left: 131px; top: 682px; display: flex; gap: 37px; }
  .teaser { width: 206px; }
  .teaser h2 { font-family: "Roboto Condensed", sans-serif; font-weight: 400; font-size: 20px; color: var(--brand-blue);
    padding-bottom: 8px; border-bottom: 2px solid var(--rule); position: relative; }
  .teaser h2::after { content: ""; position: absolute; left: 0; bottom: -2px; width: 80px; height: 2px; background: var(--brand-blue); }
  .teaser p { margin-top: 15px; font-size: 13px; line-height: 19px; font-weight: 300; color: var(--text-grey); height: 86px; }
  .read-more { display: inline-block; margin-top: 16px; width: 77px; height: 24px; line-height: 24px; text-align: center;
    background: var(--button); color: #fff; font-size: 12px; }

  .site-footer { position: absolute; left: 0; top: 923px; width: 1200px; height: 80px; background: var(--footer); }
  .footer-legal { position: absolute; left: 131px; top: 23px; font-size: 13px; line-height: 19px; color: #888; }
  .social { position: absolute; left: 960px; top: 25px; display: flex; gap: 10px; }
  .social span { width: 29px; height: 29px; background: #1f73b7; }
</style>
</head>
<body>
  <header class="site-header">
    <div class="brand"><span class="brand-dot"></span>ClearTune</div>
    <div class="contact-strip">
      <svg width="44" height="52" viewBox="0 0 44 52" aria-hidden="true">
        <path d="M14 4 C6 10 4 26 12 40 C16 46 22 48 26 46 L22 38 C18 40 15 34 14 26 C13 20 14 14 18 12 Z" fill="#333"/>
        <path d="M24 46 C34 50 40 44 38 38" stroke="#333" stroke-width="2" fill="none"/>
      </svg>
      <div class="contact-lines">
        <div>Contact us on <span class="phone">(02) 5550 1234</span></div>
        <div>or email us <span class="email">info@cleartune-example.com</span></div>
      </div>
    </div>
  </header>

  <div class="hero-band"></div>
  <nav class="main-nav">
    <span>HOME</span><span>WHAT WE DO</span><span>HOW WE DO IT</span><span>ABOUT US</span><span>GUARANTEES</span>
    <span>RESULTS</span><span>TESTIMONIALS</span><span>CONTACT</span><span>BLOG</span>
  </nav>

  <section class="slider-frame">
    <div class="slide-photo" role="img" aria-label="Red semi-trailer truck driving on a highway under a clear sky"></div>
    <svg class="slide-callout" viewBox="0 0 370 176" aria-hidden="true">
      <polygon points="8,0 370,0 370,176 48,176" fill="var(--brand-blue)"/>
      <polygon points="18,0 362,0 362,170 56,170" fill="var(--black)"/>
    </svg>
    <div class="callout-text">
      <div class="lead">We help diesel vehicle fleets</div>
      <div class="save">save up to</div>
      <div class="figure"><b>20%</b> FUEL COSTS</div>
      <div class="lead">by optimising their engines.</div>
    </div>
    <div class="partner-badge badge-one"><span></span></div>
    <div class="partner-badge badge-two"><span></span></div>
    <div class="slider-dots"><i class="active"></i><i></i><i></i></div>
  </section>

  <main class="teasers">
    <article class="teaser">
      <h2>ABOUT US</h2>
      <p>Greenway Fleet have combined over 50 years experience in all aspects of the automotive industry including commercial fleet and diesel engines. We are the ...</p>
      <span class="read-more">Read More</span>
    </article>
    <article class="teaser">
      <h2>WHAT WE DO</h2>
      <p>Greenway Fleet delivers award winning, ISO 9001 certified diesel engine ECU remapping for fleet operations. As Principal Australian Fleet Agent for ClearTune...</p>
      <span class="read-more">Read More</span>
    </article>
    <article class="teaser">
      <h2>HOW WE DO IT</h2>
      <p>Greenway Fleet will conduct an obligation Free Consultation with your Fleet Representatives to determine your Fleets needs, and identify any customization...</p>
      <span class="read-more">Read More</span>
    </article>
    <article class="teaser">
      <h2>WHY</h2>
      <p>We've acted on customer requests for cost effective, financially attractive solutions to reduce fuel and operating costs whilst also reducing environmental foot...</p>
      <span class="read-more">Read More</span>
    </article>
  </main>

  <footer class="site-footer">
    <div class="footer-legal">
      <div>Copyright 2014 cleartune. All Rights Reserved.</div>
      <div>Privacy Policy | Terms and Conditions</div>
    </div>
    <div class="social" aria-label="Social links"><span></span><span></span><span></span></div>
  </footer>
</body>
</html>
```